Personal website for my flying adventures

It is the website for my personal flying adventures.

1. I flew around the world in 2011 and became the first Chinese citizen ever flying the single engine airplane around the world in the history and also the first ever to land the single engine airplane in Halvern Ridge airport.
2. I am organizing the "Copper Kestrels Aerobatic Flying Team" in China
3. I am sharing my flying experiences regularly
4. I am writing the book about flying around the world.

Visit: www.lutanmo.com and www.tanmoskyloop.com for more information and pictures on my flying activities. Need connect two websites together well.

Target Market(s)

Young pilots

Industry/Entity Type

Airport

Requirements
Must have
• Must have the logo of "Tanmo Sky Loop"
• Must have the logo of "Copper Kestrels"
• Must have my flying pictures

```html
<!DOCTYPE html>
<html lang="en">
<head>
<meta charset="utf-8">
<title>Lu Tanmo — Flying Adventures</title>
<link rel="stylesheet" href="https://fonts.googleapis.com/css2?family=Jost:wght@400;500;700&family=Noto+Sans+SC:wght@400;700&display=swap">
<style>
  :root {
    --site-black: #050505;
    --gold: #f2c230;
    --gold-soft: #e8b93a;
    --bronze: #9a6a35;
    --white: #ffffff;
    --muted: #8a8a8a;
    --code-box: #3a3a3a;
    --label-bar: #1b1b1b;
    --arrow-box: #2a2a2a;
    --photo-sky: #c9c4bb;
    --photo-fuselage: #e9e6e0;
    --photo-stripe: #15110e;
    --photo-tarmac: #4a4139;
  }
  * { margin: 0; padding: 0; box-sizing: border-box; }
  html, body {
    width: 1200px; height: 819px; overflow: hidden;
    background: var(--site-black);
    font-family: "Jost", "Noto Sans SC", sans-serif;
    color: var(--white);
  }
  .site { position: relative; width: 1200px; height: 819px; }

  /* Header */
  .site-header { position: absolute; top: 40px; left: 0; width: 1200px; height: 55px; }
  .current-journey {
    position: absolute; left: 262px; top: 22px;
    font-size: 9px; font-weight: 700; color: var(--gold);
  }
  .route { position: absolute; left: 346px; top: 15px; display: flex; align-items: center; gap: 3px; }
  .route-code { display: flex; gap: 2px; }
  .route-code span {
    display: inline-block; width: 20px; height: 24px; line-height: 24px;
    text-align: center; background: var(--code-box); color: var(--white);
    font-size: 17px; font-weight: 500;
  }
  .route svg { margin: 0 3px; }
  .site-name {
    position: absolute; left: 547px; top: 16px;
    font-size: 19px; font-weight: 700; letter-spacing: 0.5px;
  }
  .main-nav { position: absolute; left: 692px; top: 22px; display: flex; gap: 12px; font-size: 10px; text-transform: uppercase; }
  .main-nav a { color: var(--white); text-decoration: none; }
  .main-nav a.is-active { color: var(--gold); }
  .lang-switch {
    position: absolute; left: 889px; top: 15px; width: 32px; height: 22px;
    border: 1px solid var(--gold-soft); font-size: 10px; line-height: 20px; text-align: center;
    font-family: "Noto Sans SC", sans-serif;
  }

  /* Hero */
  .hero { position: absolute; left: 40px; top: 95px; width: 1106px; height: 598px; overflow: hidden; }
  .hero-top-band { position: absolute; left: 0; top: 0; width: 100%; height: 7px; background: var(--gold); }
  .hero-bottom-band { position: absolute; left: 0; bottom: 0; width: 100%; height: 18px; background: var(--bronze); }
  .hero-photo {
    position: absolute; left: 0; top: 7px; width: 100%; height: 573px;
    background:
      radial-gradient(ellipse 34% 30% at 70% 42%, rgba(21,17,14,0.95) 0%, rgba(21,17,14,0.75) 55%, rgba(21,17,14,0) 100%),
      radial-gradient(ellipse 60% 28% at 78% 12%, rgba(233,230,224,0.95) 0%, rgba(233,230,224,0) 100%),
      linear-gradient(168deg, rgba(0,0,0,0) 38%, rgba(21,17,14,0.85) 52%, rgba(21,17,14,0.7) 64%, rgba(0,0,0,0) 76%),
      radial-gradient(ellipse 30% 40% at 12% 20%, rgba(214,210,202,0.9) 0%, rgba(214,210,202,0) 100%),
      linear-gradient(180deg, var(--photo-sky) 0%, #a6a198 40%, #6f675e 70%, var(--photo-tarmac) 100%);
  }
  .slide-arrow {
    position: absolute; top: 215px; width: 32px; height: 34px; background: var(--arrow-box);
    display: flex; align-items: center; justify-content: center;
  }
  .slide-arrow.prev { left: 0; }
  .slide-arrow.next { right: 0; }

  .hero-copy { position: absolute; left: 570px; top: 118px; width: 268px; }
  .hero-title {
    font-family: "Noto Sans SC", sans-serif; font-weight: 700;
    font-size: 44px; color: var(--gold); letter-spacing: 2px; line-height: 1.1;
  }
  .hero-text {
    margin-top: 8px; font-family: "Noto Sans SC", sans-serif;
    font-size: 10.5px; line-height: 19px; color: var(--white); font-weight: 700;
  }
  .hero-signature {
    position: absolute; left: 712px; top: 258px;
    font-family: "Noto Sans SC", sans-serif; font-size: 36px; color: var(--gold);
  }

  /* Feature tiles */
  .feature-tiles { position: absolute; left: 235px; top: 373px; display: flex; }
  .feature-tile { width: 211px; }
  .tile-image { position: relative; height: 118px; }
  .tile-image.journey { background: linear-gradient(160deg, #e4e4e4 0%, #9c9c9c 55%, #4a4a4a 100%); }
  .tile-image.sky-loop { background: linear-gradient(180deg, #3f8fd8 0%, #9fcdf0 60%, #e8f3fb 100%); }
  .tile-image.kestrels { background: linear-gradient(160deg, #3d63c4 0%, #5c86d8 55%, #8fb2ea 100%); }
  .tile-heading { position: absolute; font-weight: 700; color: var(--gold); line-height: 1.05; }
  .journey .tile-heading { left: 12px; bottom: 8px; font-size: 19px; }
  .sky-loop .tile-heading { left: 10px; top: 14px; font-size: 14px; color: #e23b2a; width: 120px; }
  .kestrels .tile-heading { left: 40px; top: 16px; font-size: 13px; width: 130px; }
  .tile-label {
    height: 38px; background: var(--label-bar); display: flex; align-items: center;
    justify-content: space-between; padding: 0 10px 0 18px; font-size: 10.5px; color: var(--white);
  }

  /* Footer */
  .site-footer { position: absolute; left: 0; top: 714px; width: 1200px; height: 20px; font-size: 9.5px; }
  .footer-links { position: absolute; left: 466px; top: 0; display: flex; gap: 18px; }
  .footer-links a { color: #cfcfcf; text-decoration: none; text-transform: uppercase; }
  .footer-links a.cn { font-family: "Noto Sans SC", sans-serif; text-transform: none; }
  .copyright { position: absolute; left: 942px; top: 1px; font-size: 8px; color: var(--muted); }
</style>
</head>
<body>
<div class="site">
  <header class="site-header">
    <div class="current-journey">Current Journey</div>
    <div class="route">
      <div class="route-code"><span>M</span><span>E</span><span>M</span></div>
      <svg width="18" height="14" viewBox="0 0 18 14" aria-hidden="true">
        <path d="M1 7 H15 M10 2 L15 7 L10 12" stroke="#ffffff" stroke-width="2" fill="none"/>
      </svg>
      <div class="route-code"><span>D</span><span>C</span><span>A</span></div>
    </div>
    <div class="site-name">LU TANMO</div>
    <nav class="main-nav">
      <a href="#">About</a>
      <a href="#" class="is-active">Photos</a>
      <a href="#">Journal</a>
      <a href="#">Itinerary</a>
    </nav>
    <div class="lang-switch">中文</div>
  </header>

  <section class="hero">
    <div class="hero-top-band"></div>
    <div class="hero-photo" role="img" aria-label="Photo of the pilot in uniform seated on the wing of a white and black single engine plane on the airport apron"></div>

    <div class="slide-arrow prev">
      <svg width="10" height="14" viewBox="0 0 10 14" aria-hidden="true"><path d="M7 2 L2 7 L7 12" stroke="#ffffff" stroke-width="2" fill="none"/></svg>
    </div>
    <div class="slide-arrow next">
      <svg width="10" height="14" viewBox="0 0 10 14" aria-hidden="true"><path d="M3 2 L8 7 L3 12" stroke="#f2c230" stroke-width="2" fill="none"/></svg>
    </div>

    <div class="hero-copy">
      <h1 class="hero-title">快乐飞翔</h1>
      <p class="hero-text">飞行，是我一生的热爱。在中国，天空曾经遥远；在世界，飞行是自由的语言。随着通用航空的发展，每个人都能追寻飞行的梦想。我希望用自己的旅程，激励更多年轻飞行员，推动中国的发展！</p>
    </div>
    <div class="hero-signature">陆坦谟</div>

    <div class="feature-tiles">
      <article class="feature-tile">
        <div class="tile-image journey" role="img" aria-label="Photo of a small plane in flight">
          <span class="tile-heading">JOURNEY</span>
        </div>
        <div class="tile-label"><span>My latest journey and inspirations</span>
          <svg width="8" height="12" viewBox="0 0 8 12" aria-hidden="true"><path d="M2 1 L7 6 L2 11" stroke="#ffffff" stroke-width="2" fill="none"/></svg>
        </div>
      </article>
      <article class="feature-tile">
        <div class="tile-image sky-loop" role="img" aria-label="Sky banner for the round the world flight">
          <span class="tile-heading">TANMO SKY LOOP</span>
        </div>
        <div class="tile-label"><span>My latest journey and inspirations</span>
          <svg width="8" height="12" viewBox="0 0 8 12" aria-hidden="true"><path d="M2 1 L7 6 L2 11" stroke="#ffffff" stroke-width="2" fill="none"/></svg>
        </div>
      </article>
      <article class="feature-tile">
        <div class="tile-image kestrels" role="img" aria-label="Aerobatic planes trailing smoke in a blue sky">
          <span class="tile-heading">COPPER KESTRELS AEROBATIC FLYING TEAM</span>
        </div>
        <div class="tile-label"><span>Aerobatic Team</span>
          <svg width="8" height="12" viewBox="0 0 8 12" aria-hidden="true"><path d="M2 1 L7 6 L2 11" stroke="#ffffff" stroke-width="2" fill="none"/></svg>
        </div>
      </article>
    </div>

    <div class="hero-bottom-band"></div>
  </section>

  <footer class="site-footer">
    <div class="footer-links">
      <a href="#">Facepage</a>
      <a href="#">Chirper</a>
      <a href="#" class="cn">陆坦谟飞行网站</a>
      <a href="#" class="cn">环球飞行中文网站</a>
    </div>
    <div class="copyright">Copyright 2013 LuTanmo All rights reserved.</div>
  </footer>
</div>
</body>
</html>
```